Bramblewood Card Company Business Cards

We are a trading card store with Glimmorax, sports and other TCG cards, we need a business card design that encompasses a clean cut, modern style with a retro flare. website is bramblewoodcardco.com for reference. Can utilize a comic book era feel or a more modern outdoor feel to utilize the "Pacific Northwest" elements of tress, mountains, etc.

Industry/Entity Type

Trading cards and collectibles

Contact Information for Business Card

business name, email address, phone number, name, owner job title

Font styles to use
Sans Serif

```html
<!DOCTYPE html>
<html lang="en">
<head>
<meta charset="utf-8">
<title>Bramblewood Card Company Business Cards</title>
<link href="https://fonts.googleapis.com/css2?family=Montserrat:wght@400;500;700&display=swap" rel="stylesheet">
<style>
  :root {
    --backdrop: #d3d6d7;
    --paper: #f7f7f6;
    --teal: #12b4d6;
    --teal-deep: #0d9cc0;
    --ink: #3e3f41;
    --ink-soft: #444;
    --wave-line: #3a3a3c;
  }
  * { margin: 0; padding: 0; box-sizing: border-box; }
  html, body { width: 1200px; height: 829px; overflow: hidden; }
  body {
    background: var(--backdrop);
    font-family: "Montserrat", sans-serif;
    position: relative;
  }
  .card {
    position: absolute;
    top: 266px;
    width: 520px;
    height: 297px;
    border-radius: 3px;
    overflow: hidden;
    box-shadow: 0 10px 26px rgba(0,0,0,0.16);
  }
  .card-front { left: 53px; background: var(--paper); }
  .card-back { left: 627px; background: var(--teal); display: flex; align-items: center; justify-content: center; }

  .front-wave { position: absolute; inset: 0; width: 100%; height: 100%; }

  .accent-bar {
    position: absolute; left: 0; top: 34px;
    width: 26px; height: 24px; background: var(--teal);
  }
  .holder-name {
    position: absolute; left: 42px; top: 30px;
    font-weight: 700; font-size: 25px; line-height: 30px; letter-spacing: 1.5px;
    color: var(--teal); text-transform: uppercase;
  }
  .holder-title {
    position: absolute; left: 42px; top: 62px;
    font-weight: 400; font-size: 15px; line-height: 20px; color: var(--ink-soft);
  }
  .address {
    position: absolute; left: 42px; top: 98px;
    font-size: 15px; line-height: 21px; color: var(--ink-soft);
  }
  .contact-list {
    position: absolute; left: 24px; top: 144px;
    list-style: none; font-size: 15px; line-height: 23px; color: var(--ink-soft);
  }
  .contact-list li { display: flex; align-items: center; gap: 8px; white-space: nowrap; }
  .contact-list svg { width: 12px; height: 12px; flex: none; }

  .company-mark {
    position: absolute; right: 22px; top: 100px; width: 170px;
    text-align: center; font-weight: 700; font-size: 18px; line-height: 24px;
    color: var(--ink); text-transform: uppercase; letter-spacing: 1px;
  }
  .card-back .company-mark {
    position: static; width: 280px; font-size: 26px; line-height: 34px;
  }
</style>
</head>
<body>
  <section class="card card-front">
    <svg class="front-wave" viewBox="0 0 520 297" preserveAspectRatio="none" aria-hidden="true">
      <path d="M0,226 C40,248 140,244 250,254 C360,264 440,272 490,297 L0,297 Z" fill="var(--wave-line)"/>
      <path d="M0,231 C40,256 140,253 250,263 C350,272 420,280 460,297 L0,297 Z" fill="var(--teal-deep)"/>
    </svg>
    <div class="accent-bar"></div>
    <h1 class="holder-name">Dorian Hale</h1>
    <p class="holder-title">CEO/Founder</p>
    <p class="address">P.O. Box 318 Alder Lane<br>Olympia WA 98501</p>
    <ul class="contact-list">
      <li>
        <svg viewBox="0 0 12 12"><path d="M2.5 1 L4.5 1 L5.2 3.5 L4 4.5 C4.6 6 6 7.4 7.5 8 L8.5 6.8 L11 7.5 L11 9.5 C11 10.3 10.3 11 9.5 11 C5 11 1 7 1 2.5 C1 1.7 1.7 1 2.5 1 Z" fill="var(--teal)"/></svg>
        (360) 555 0148
      </li>
      <li>
        <svg viewBox="0 0 12 12"><rect x="0.5" y="2" width="11" height="8" fill="var(--teal)"/><path d="M0.5 2 L6 6.5 L11.5 2" fill="none" stroke="#fff" stroke-width="1"/></svg>
        info@bramblewoodcardco.com
      </li>
      <li>
        <svg viewBox="0 0 12 12"><circle cx="6" cy="6" r="5.2" fill="none" stroke="var(--teal)" stroke-width="1.2"/><ellipse cx="6" cy="6" rx="2.2" ry="5.2" fill="none" stroke="var(--teal)" stroke-width="1"/><line x1="0.8" y1="6" x2="11.2" y2="6" stroke="var(--teal)" stroke-width="1"/></svg>
        www.bramblewoodcardco.com
      </li>
    </ul>
    <p class="company-mark">Bramblewood Card Company</p>
  </section>

  <section class="card card-back">
    <p class="company-mark">Bramblewood Card Company</p>
  </section>
</body>
</html>
```